North Carolina-themed postcard

Would like 3x distinct designs for a postcard (sized 4.5 x 5.5) that celebrates the state of North Carolina. A vintage theme, a modern theme, and a simple black/white theme would be suggestions for design styles.

```html
<!DOCTYPE html>
<html lang="en">
<head>
<meta charset="utf-8">
<title>Greetings from North Carolina – Postcard</title>
<link rel="stylesheet" href="https://fonts.googleapis.com/css2?family=Chewy&family=Great+Vibes&family=Open+Sans:wght@700&display=swap">
<style>
  :root {
    --stage: #d6d6d6;
    --paper: #ffffff;
    --ghost-light: #f3f3f3;
    --ghost-dark: #d9d9d9;
    --ink: #1c1c1c;
    --sky-top: #f6f9fb;
    --sky-bottom: #cde0ea;
    --blue: #25a3dc;
    --navy: #2b2f36;
    --script-navy: #1f2f6b;
    --script-red: #c2304a;
    --letter-rim: #e0445a;
    --photo-gold: #b9985a;
    --photo-dusk: #3c4a6a;
    --leaf: #8bb46a;
  }
  * { margin: 0; padding: 0; box-sizing: border-box; }
  html, body { width: 1200px; height: 696px; overflow: hidden; background: var(--stage); }
  .canvas { position: relative; width: 1200px; height: 696px; }

  .postcard {
    position: absolute;
    top: 158px;
    width: 550px;
    height: 380px;
    background: var(--paper);
    box-shadow: 0 6px 18px rgba(0,0,0,.22);
    overflow: hidden;
  }
  .postcard--back { left: 34px; }
  .postcard--front { left: 616px; }

  .back-ghost-photo {
    position: absolute; inset: 0;
    background: radial-gradient(ellipse at 35% 45%, var(--ghost-dark), var(--ghost-light) 70%);
    opacity: .8;
  }
  .back-layout { position: absolute; inset: 0; }

  .front-art { position: absolute; inset: 0; }
  .greeting-script { font-family: "Great Vibes", cursive; }
  .state-name { font-family: "Chewy", system-ui, sans-serif; }
  .photo-caption { font-family: "Open Sans", Arial, sans-serif; font-weight: 700; }
</style>
</head>
<body>
<main class="canvas">

  <!-- Address side -->
  <section class="postcard postcard--back" aria-label="Postcard address side">
    <div class="back-ghost-photo" role="img" aria-label="Faded black and white photo of the State Capitol with statue"></div>
    <svg class="back-layout" viewBox="0 0 550 380" width="550" height="380">
      <line x1="300" y1="30" x2="300" y2="350" stroke="var(--ink)" stroke-width="1.2"/>
      <rect class="stamp-box" x="440" y="35" width="80" height="60" fill="none" stroke="var(--ink)" stroke-width="1.4"/>
      <g class="address-lines" stroke="var(--ink)" stroke-width="1.1">
        <line x1="325" y1="170" x2="520" y2="170"/>
        <line x1="325" y1="210" x2="520" y2="210"/>
        <line x1="325" y1="250" x2="520" y2="250"/>
        <line x1="325" y1="290" x2="520" y2="290"/>
      </g>
    </svg>
  </section>

  <!-- Picture side -->
  <section class="postcard postcard--front" aria-label="Postcard picture side">
    <svg class="front-art" viewBox="0 0 550 380" width="550" height="380">
      <defs>
        <linearGradient id="sky" x1="0" y1="0" x2="0.4" y2="1">
          <stop offset="0" stop-color="var(--sky-top)"/>
          <stop offset="1" stop-color="var(--sky-bottom)"/>
        </linearGradient>
        <linearGradient id="script" x1="0" y1="1" x2="1" y2="0">
          <stop offset="0" stop-color="var(--script-navy)"/>
          <stop offset="0.6" stop-color="var(--script-navy)"/>
          <stop offset="1" stop-color="var(--script-red)"/>
        </linearGradient>
        <linearGradient id="letterFill" x1="0" y1="0" x2="0" y2="1">
          <stop offset="0" stop-color="#7fb6e0"/>
          <stop offset="0.55" stop-color="#5f8f9a"/>
          <stop offset="1" stop-color="#4d7d3c"/>
        </linearGradient>
        <linearGradient id="capitolPhoto" x1="0" y1="0" x2="0" y2="1">
          <stop offset="0" stop-color="var(--photo-dusk)"/>
          <stop offset="0.35" stop-color="var(--photo-gold)"/>
          <stop offset="1" stop-color="#5b5a3a"/>
        </linearGradient>
        <radialGradient id="blossom" cx="0.5" cy="0.45" r="0.55">
          <stop offset="0" stop-color="#ffffff"/>
          <stop offset="0.55" stop-color="#e3eef2"/>
          <stop offset="1" stop-color="var(--leaf)" stop-opacity="0"/>
        </radialGradient>
      </defs>

      <rect class="card-ground" width="550" height="380" fill="url(#sky)"/>

      <polygon class="dark-panel" points="300,0 550,0 550,225 430,225 300,100" fill="var(--navy)"/>
      <polygon class="accent-stripe" points="300,0 318,0 318,55 300,55" fill="var(--blue)"/>
      <polygon class="accent-stripe" points="350,0 376,0 376,170 350,170" fill="var(--blue)"/>

      <polygon class="lower-blue" points="420,230 550,190 550,330 370,330" fill="var(--blue)"/>
      <rect class="bottom-band" x="0" y="330" width="550" height="50" fill="var(--blue)"/>

      <g role="img" aria-label="Photo of the State Capitol building with bronze statue at dusk">
        <rect x="400" y="28" width="142" height="220" fill="url(#capitolPhoto)"/>
      </g>
      <rect class="caption-bar" x="400" y="28" width="142" height="20" fill="var(--navy)" opacity=".75"/>
      <text class="photo-caption" x="406" y="42" font-size="10.5" fill="#ffffff">State Capitol In Raleigh</text>
      <polyline class="frame-line" points="396,24 546,24 546,300 430,300 396,266 396,24" fill="none" stroke="#ffffff" stroke-width="1.5"/>
      <circle class="hang-ring" cx="338" cy="30" r="6" fill="none" stroke="#ffffff" stroke-width="1.4"/>

      <g role="img" aria-label="Illustration of a white dogwood blossom with green leaves">
        <ellipse cx="150" cy="115" rx="95" ry="65" fill="url(#blossom)"/>
      </g>

      <text class="greeting-script" x="40" y="120" font-size="58" fill="url(#script)" stroke="#ffffff" stroke-width="3" paint-order="stroke">Greetings</text>
      <text class="greeting-script" x="150" y="172" font-size="54" fill="url(#script)" stroke="#ffffff" stroke-width="3" paint-order="stroke">from</text>

      <g class="state-name" transform="rotate(-24 120 300)">
        <text x="123" y="304" font-size="66" fill="var(--letter-rim)">NORTH</text>
        <text x="120" y="300" font-size="66" fill="url(#letterFill)" stroke="#ffffff" stroke-width="2" paint-order="stroke">NORTH</text>
      </g>
      <g class="state-name" transform="rotate(-24 215 335)">
        <text x="218" y="339" font-size="66" fill="var(--letter-rim)">CAROLINA</text>
        <text x="215" y="335" font-size="66" fill="url(#letterFill)" stroke="#ffffff" stroke-width="2" paint-order="stroke">CAROLINA</text>
      </g>
    </svg>
  </section>

</main>
</body>
</html>
```